National Mission Critical Construction Contractor needs Stationery Design to make a bold statement

We are a small commercial construction company, working primarily in mission critical facilities across the U.S.. We have exciting corporate changes going an and a new logo and office space so we need new stationery. The final design should incorporate our new logo and invoke a fresh, high-tech feel while looking simple and modern.

Industry/Entity Type

Construction

Contact Information for Business Card

We are required to list our state licensing qualifications on the back of our card.

Font styles to use
Sans Serif

Requirements
Must have
• We need to have a design for second page of stationery, envelopes both standard and with a window and for a 3 x 4 notepad.

```html
<!DOCTYPE html>
<html lang="en">
<head>
<meta charset="utf-8">
<title>Northford Construction Management — Letterhead</title>
<link rel="stylesheet" href="https://fonts.googleapis.com/css2?family=Source+Sans+3:wght@400;600&display=swap">
<style>
  :root {
    --brand-navy: #0c6fb6;
    --brand-sky: #2aa9e1;
    --brand-green: #8cc63f;
    --paper: #ffffff;
    --ghost: #eaf2f9;
    --ink: #0c6fb6;
  }
  html, body {
    margin: 0;
    padding: 0;
    overflow: hidden;
    background: var(--paper);
  }
  .letterhead {
    position: relative;
    width: 927px;
    height: 1200px;
    overflow: hidden;
    background: var(--paper);
    font-family: "Source Sans 3", sans-serif;
  }
  .header-band {
    position: absolute;
    left: 0;
    top: 0;
    width: 927px;
    height: 120px;
    background: linear-gradient(90deg, var(--brand-navy) 0%, var(--brand-sky) 55%, var(--brand-green) 100%);
  }

  .company-name {
    position: absolute;
    right: 60px;
    top: 236px;
    text-align: right;
    color: var(--ink);
    font-weight: 600;
    line-height: 1;
  }
  .company-name__main {
    display: block;
    font-size: 44px;
    letter-spacing: 2px;
  }
  .company-name__sub {
    display: block;
    margin-top: 12px;
    font-size: 13px;
    letter-spacing: 4.4px;
  }

  .ghost-name {
    position: absolute;
    left: 0;
    right: 0;
    top: 690px;
    text-align: center;
    color: var(--ghost);
    font-weight: 600;
    line-height: 1;
  }
  .ghost-name__main {
    display: block;
    font-size: 108px;
    letter-spacing: 8px;
  }
  .ghost-name__sub {
    display: block;
    margin-top: 28px;
    font-size: 37px;
    letter-spacing: 11px;
  }

  .contact-bar {
    position: absolute;
    left: 30px;
    right: 28px;
    top: 1141px;
    display: flex;
    justify-content: space-between;
    align-items: center;
    color: var(--ink);
    font-size: 13px;
  }
  .contact-item {
    display: flex;
    align-items: center;
    gap: 4px;
  }
  .contact-item svg {
    width: 15px;
    height: 15px;
    fill: var(--ink);
  }
  .contact-item__divider {
    width: 1.5px;
    height: 18px;
    background: var(--ink);
    margin-right: 3px;
  }
  .footer-band {
    position: absolute;
    left: 0;
    bottom: 0;
    width: 927px;
    height: 33px;
    background: var(--brand-navy);
  }
</style>
</head>
<body>
<main class="letterhead">
  <div class="header-band" role="img" aria-label="Decorative header bands in navy, sky blue and green"></div>

  <div class="company-name">
    <span class="company-name__main">NORTHFORD</span>
    <span class="company-name__sub">CONSTRUCTION MANAGEMENT</span>
  </div>

  <div class="ghost-name" aria-hidden="true">
    <span class="ghost-name__main">NORTHFORD</span>
    <span class="ghost-name__sub">CONSTRUCTION MANAGEMENT</span>
  </div>

  <footer class="contact-bar">
    <div class="contact-item">
      <svg viewBox="0 0 16 16" aria-hidden="true"><path d="M1,2 H15 V14 H1 Z M2.2,3.2 V12.8 H13.8 V3.2 Z M2.6,3.6 L8,8.6 L13.4,3.6 L14,4.3 L10,8 L14,11.8 L13.4,12.4 L9.3,8.6 L8,9.8 L6.7,8.6 L2.6,12.4 L2,11.8 L6,8 L2,4.3 Z"/></svg>
      <span class="contact-item__divider"></span>
      <span>418 street carson, nevada</span>
    </div>
    <div class="contact-item">
      <svg viewBox="0 0 16 16" aria-hidden="true"><circle cx="8" cy="8" r="8"/><path fill="#fff" d="M5,3.8 L6.6,3.6 L7.4,5.8 L6.4,6.8 C6.9,8 7.9,9 9.2,9.6 L10.2,8.6 L12.4,9.4 L12.2,11 C9,11.4 4.6,7 5,3.8 Z"/></svg>
      <span class="contact-item__divider"></span>
      <span>(555)-014-2768</span>
    </div>
    <div class="contact-item">
      <svg viewBox="0 0 16 16" aria-hidden="true"><path d="M8,0.5 C4.9,0.5 2.6,2.8 2.6,5.8 C2.6,9.6 8,15.5 8,15.5 C8,15.5 13.4,9.6 13.4,5.8 C13.4,2.8 11.1,0.5 8,0.5 Z M8,3.6 A2.2,2.2 0 1 1 7.99,3.6 Z"/></svg>
      <span class="contact-item__divider"></span>
      <span>northford@mail.com</span>
    </div>
  </footer>

  <div class="footer-band"></div>
</main>
</body>
</html>
```